Product Designer Business Card

Small product design, engineering and prototyping firm in need of a clean, professional business card design. To support our 3D design and drawing services, we offer 3D printing, molding, and casting of plastics, silicones, resins, etc. Our logo can still be modified/changed if necessary. The red/orange color is preferred, but may be substituted with blue or green, potentially. Either way, the colour of the logo should be match/compliment colors used throughout the design. One thought is to have the logo/contact info on one side, with the other side describing services offered, like with a small icon of 3D printer, molding, casting, and computer with a 3D model on-screen.
Industry/Entity Type
Mechanical Engineering
Contact Information for Business Card
Company: Kelvar Design
Phone: 613-582-9047
Email: mark@kelvardesign.ca

```html
<!DOCTYPE html>
<html lang="en">
<head>
<meta charset="utf-8">
<title>Kelvar Design — Business Card</title>
<link href="https://fonts.googleapis.com/css2?family=Work+Sans:wght@400;500;600&display=swap" rel="stylesheet">
<style>
  :root {
    --backdrop: #1a1a1a;
    --card: #232323;
    --card-edge: #2c2c2c;
    --accent: #e8290b;
    --accent-soft: #5a1a10;
    --ink: #f2f2f2;
    --ink-muted: #d8d8d8;
  }
  * { box-sizing: border-box; margin: 0; padding: 0; }
  html, body {
    width: 1200px; height: 900px; overflow: hidden;
    background: var(--backdrop);
    font-family: "Work Sans", Arial, sans-serif;
  }
  .canvas {
    width: 1200px; height: 900px;
    display: flex; flex-direction: column; align-items: center; justify-content: center;
    gap: 44px;
  }
  .card {
    width: 640px; height: 366px;
    background: linear-gradient(135deg, var(--card) 0%, var(--card-edge) 100%);
    position: relative;
  }

  /* Front */
  .card-front {
    display: flex; align-items: center; justify-content: center; gap: 22px;
  }
  .brand-dot {
    width: 46px; height: 46px; border-radius: 50%;
    background: var(--accent);
  }
  .brand-name {
    color: var(--ink);
    font-weight: 600; font-size: 44px; letter-spacing: 4px;
  }

  /* Back */
  .services {
    position: absolute; top: 54px; left: 0; right: 0;
    display: flex; justify-content: center; gap: 56px;
  }
  .service { display: flex; flex-direction: column; align-items: center; gap: 12px; }
  .service-icon {
    width: 110px; height: 104px; border-radius: 6px;
    background: linear-gradient(160deg, var(--accent) 0%, var(--accent-soft) 100%);
  }
  .service-label { color: var(--ink); font-weight: 500; font-size: 21px; }

  .contact {
    position: absolute; left: 70px; right: 40px; bottom: 52px;
    display: flex; align-items: center; gap: 22px;
  }
  .person { text-align: right; }
  .person-name {
    color: var(--accent); font-weight: 500; font-size: 22px;
    letter-spacing: 1px; text-transform: uppercase;
  }
  .person-title { color: var(--ink-muted); font-size: 18px; letter-spacing: 1px; }
  .divider { width: 2px; height: 52px; background: var(--accent); }
  .contact-lines { display: flex; flex-direction: column; gap: 6px; }
  .contact-line {
    display: flex; align-items: center; gap: 8px;
    color: var(--ink); font-size: 18px; letter-spacing: 1px;
  }
  .contact-line svg { width: 14px; height: 14px; flex: none; }
</style>
</head>
<body>
<main class="canvas">
  <section class="card card-front" aria-label="Card front">
    <span class="brand-dot" aria-hidden="true"></span>
    <h1 class="brand-name">Kelvar Design</h1>
  </section>

  <section class="card card-back" aria-label="Card back">
    <div class="services">
      <div class="service">
        <div class="service-icon" role="img" aria-label="Line icon of a molding press"></div>
        <span class="service-label">Molding</span>
      </div>
      <div class="service">
        <div class="service-icon" role="img" aria-label="Line icon of a 3D printer"></div>
        <span class="service-label">3D printer</span>
      </div>
      <div class="service">
        <div class="service-icon" role="img" aria-label="Line icon for casting"></div>
        <span class="service-label">Casting</span>
      </div>
    </div>

    <div class="contact">
      <div class="person">
        <p class="person-name">Daniel Reeve</p>
        <p class="person-title">President</p>
      </div>
      <span class="divider" aria-hidden="true"></span>
      <div class="contact-lines">
        <p class="contact-line">
          <svg viewBox="0 0 24 24" aria-hidden="true"><path fill="#e8290b" d="M6.6 10.8a15.1 15.1 0 0 0 6.6 6.6l2.2-2.2c.3-.3.7-.4 1-.2 1.1.4 2.3.6 3.6.6.6 0 1 .4 1 1V20c0 .6-.4 1-1 1A17 17 0 0 1 3 4c0-.6.4-1 1-1h3.5c.6 0 1 .4 1 1 0 1.3.2 2.5.6 3.6.1.3 0 .7-.2 1z"/></svg>
          613-582-9047
        </p>
        <p class="contact-line">
          <svg viewBox="0 0 24 24" aria-hidden="true"><rect x="2.5" y="5" width="19" height="14" rx="1.5" fill="none" stroke="#e8290b" stroke-width="2"/><path d="M3 6l9 7 9-7" fill="none" stroke="#e8290b" stroke-width="2"/></svg>
          mark@kelvardesign.ca
        </p>
      </div>
    </div>
  </section>
</main>
</body>
</html>
```